Alloy wheel repair business needs a website

Install logo previously purchased from makerhive, toolbar with dropdowns. services, gallery, clients , contact ect
Maybe mission statment

Target Market(s)

vehicle owners, auto dealers,insurance companies,

Industry/Entity Type

Alloy Wheel Repair

Coding

Coded - Design and coding required

Number of Pages Required

4 page

Font styles to use
Sans Serif

Colors
0054AA
0677BA
7BADD7
CADEEF
E8F1F8

```html
<!DOCTYPE html>
<html lang="en">
<head>
<meta charset="utf-8">
<title>Rimcraft Works – Alloy Wheel Repair</title>
<link href="https://fonts.googleapis.com/css2?family=Arimo:wght@400;700&family=Syncopate:wght@700&family=Tinos&display=swap" rel="stylesheet">
<style>
:root{
  --blue:#4485c6;
  --blue-dark:#0054AA;
  --blue-mid:#0677BA;
  --blue-light:#7BADD7;
  --blue-pale:#CADEEF;
  --ink:#111;
  --text:#222;
  --white:#fff;
  --black:#000;
}
*{box-sizing:border-box;margin:0;padding:0}
html,body{width:1200px;height:3125px;overflow:hidden;background:var(--white)}
body{position:relative;font-family:'Arimo',Arial,sans-serif;color:var(--text)}
.abs{position:absolute}
.display{font-family:'Syncopate','Arial Black',sans-serif;font-weight:700;color:var(--ink);text-transform:uppercase}
.btn{position:absolute;display:flex;align-items:center;justify-content:center;background:var(--blue);color:var(--white);border-radius:4px;font-size:16px}

/* header */
.site-header{left:0;top:0;width:1200px;height:74px;background:var(--white)}
.brand{left:113px;top:16px;display:flex;align-items:center;gap:8px;font-family:'Arimo',sans-serif;font-weight:700;font-size:22px;color:var(--blue);letter-spacing:1px}
.brand-dot{width:14px;height:14px;border-radius:50%;background:var(--blue)}
.nav a{position:absolute;top:28px;font-size:15px;color:var(--ink);text-decoration:none}
.search-btn{left:993px;top:18px;width:94px;height:43px;font-size:15px;gap:6px}

/* hero */
.hero{left:0;top:74px;width:1200px;height:643px;background:radial-gradient(ellipse at 62% 45%,#4a4843 0%,#2a2926 40%,#121212 100%)}
.hero-welcome{left:0;width:1200px;top:160px;text-align:center;color:var(--white);font-weight:700;font-size:26px}
.hero-title{left:0;width:1200px;top:202px;text-align:center;color:var(--white);font-size:66px;line-height:78px;letter-spacing:2px}
.hero-lead{left:200px;width:800px;top:352px;text-align:center;color:var(--white);font-size:19.5px;line-height:32px}
.hero-cta{left:524px;top:442px;width:132px;height:47px;border:2px solid var(--white);border-radius:7px;color:var(--white);font-size:20px;display:flex;align-items:center;justify-content:center}

.section-title{left:0;width:1200px;text-align:center;font-size:36px;letter-spacing:1px}

/* services */
.service-card{width:224px;height:278px;top:841px;background:var(--white);box-shadow:0 2px 10px rgba(0,0,0,.16);border-radius:3px;text-align:center}
.service-card svg{position:absolute;left:84px;top:20px}
.service-card h3{position:absolute;top:90px;width:100%;font-size:15px;color:var(--ink)}
.service-card p{position:absolute;top:118px;left:12px;right:12px;font-size:14.5px;line-height:24px;color:var(--ink)}
.service-card .btn{left:56px;top:218px;width:114px;height:44px}
.chev{top:958px}

/* gallery */
.photo{border-radius:6px}

/* mission */
.mission-frame{left:182px;top:2040px;width:308px;height:329px;border:12px solid var(--black);border-top:none}
.mission-photo{left:142px;top:2016px;width:397px;height:320px;background:linear-gradient(135deg,#9a9a98,#555654 55%,#2c2c2c)}
.mission-text{left:599px;top:2010px;width:490px;font-size:15.5px;line-height:25.8px;color:var(--ink)}

/* clients */
.footer{left:0;top:2828px;width:1200px;height:297px;background:var(--black)}
.clients-box{left:182px;top:2454px;width:835px;height:407px;background:var(--white);box-shadow:0 0 8px rgba(0,0,0,.12)}
.client-ring{left:294px;top:2600px;width:196px;height:196px;border-radius:50%;border:14px solid var(--blue);background:var(--white)}
.client-photo{left:16px;top:16px;width:136px;height:136px;border-radius:50%;background:linear-gradient(160deg,#c9b9a8,#7a5c46 60%,#3a2a22)}
.client-quote{left:601px;top:2600px;width:378px;font-size:15.5px;line-height:25.8px;color:var(--ink)}
.quote-mark{font-family:'Tinos',serif;font-size:74px;color:#555;line-height:1}
.arrow-btn{top:2651px;width:39px;height:38px;border-radius:4px;background:var(--blue-light)}

/* footer */
.footer-brand{left:0;width:1200px;top:2906px;display:flex;justify-content:center;align-items:center;gap:8px;color:var(--white);font-weight:700;font-size:22px;letter-spacing:1px}
.footer-brand .brand-dot{background:var(--white)}
.footer-nav a{position:absolute;top:2979px;color:var(--white);font-size:15px;text-decoration:none}
.footer-contact{left:0;width:1200px;top:3032px;display:flex;justify-content:center;gap:30px;color:var(--white);font-family:'Tinos',serif;font-size:20px}
.footer-contact span{display:flex;align-items:center;gap:8px}
.copyright{left:0;width:1200px;top:3094px;text-align:center;color:var(--white);font-family:'Tinos',serif;font-size:12.5px}
</style>
</head>
<body>

<header class="abs site-header">
  <div class="abs brand"><span class="brand-dot"></span>RIMCRAFT WORKS</div>
  <nav class="nav">
    <a style="left:510px">Home</a>
    <a style="left:598px">Services</a>
    <a style="left:704px">Gallery</a>
    <a style="left:800px">Clients</a>
    <a style="left:895px">Contact</a>
  </nav>
  <div class="btn search-btn">Search
    <svg width="14" height="14" viewBox="0 0 14 14"><circle cx="6" cy="6" r="4.5" fill="none" stroke="#fff" stroke-width="1.6"/><line x1="9.3" y1="9.3" x2="13" y2="13" stroke="#fff" stroke-width="1.6"/></svg>
  </div>
</header>

<section class="abs hero" role="img" aria-label="Mechanic's hand resting on a tyre in a dark workshop"></section>
<div class="abs hero-welcome">Welcome</div>
<h1 class="abs display hero-title">Rimcraft<br>Works</h1>
<p class="abs hero-lead">perspiciatis unde omnis iste natus error sit voluptatem accusantium doloremque laudantium, totam rem aperiam, eaque</p>
<div class="abs hero-cta">Get Started</div>

<h2 class="abs display section-title" style="top:754px">Services</h2>
<svg class="abs chev" style="left:93px" width="20" height="30" viewBox="0 0 20 30"><polyline points="15,3 5,15 15,27" fill="none" stroke="#666" stroke-width="3"/></svg>
<svg class="abs chev" style="left:1087px" width="20" height="30" viewBox="0 0 20 30"><polyline points="5,3 15,15 5,27" fill="none" stroke="#666" stroke-width="3"/></svg>

<article class="abs service-card" style="left:112px">
  <svg width="56" height="56" viewBox="0 0 56 56"><circle cx="28" cy="28" r="25" fill="none" stroke="var(--blue)" stroke-width="5"/><circle cx="28" cy="28" r="16" fill="none" stroke="var(--blue)" stroke-width="3"/><circle cx="28" cy="28" r="5" fill="var(--blue)"/><g stroke="var(--blue)" stroke-width="3"><line x1="28" y1="12" x2="28" y2="44"/><line x1="12" y1="28" x2="44" y2="28"/></g></svg>
  <h3>Lorem Ipsum</h3>
  <p>Sed ut perspiciatis unde omnis iste natus error sit voluptatem accusantium doloremque laudantium</p>
  <div class="btn">Read More</div>
</article>
<article class="abs service-card" style="left:363px">
  <svg width="56" height="56" viewBox="0 0 56 56"><circle cx="32" cy="26" r="22" fill="none" stroke="var(--blue)" stroke-width="2.5"/><circle cx="32" cy="26" r="13" fill="none" stroke="var(--blue)" stroke-width="2"/><circle cx="32" cy="26" r="4" fill="var(--blue)"/><path d="M4 46 Q16 36 24 44 L36 50 L8 52 Z" fill="none" stroke="var(--blue)" stroke-width="2.5"/></svg>
  <h3>Lorem Ipsum</h3>
  <p>Sed ut perspiciatis unde omnis iste natus error sit voluptatem accusantium doloremque laudantium</p>
  <div class="btn">Read More</div>
</article>
<article class="abs service-card" style="left:613px">
  <svg width="56" height="56" viewBox="0 0 56 56"><circle cx="30" cy="26" r="22" fill="none" stroke="var(--blue)" stroke-width="2.5"/><circle cx="30" cy="26" r="12" fill="none" stroke="var(--blue)" stroke-width="2"/><circle cx="30" cy="26" r="3.5" fill="var(--blue)"/><line x1="8" y1="50" x2="24" y2="32" stroke="var(--blue)" stroke-width="4" stroke-linecap="round"/></svg>
  <h3>Lorem Ipsum</h3>
  <p>Sed ut perspiciatis unde omnis iste natus error sit voluptatem accusantium doloremque laudantium</p>
  <div class="btn">Read More</div>
</article>
<article class="abs service-card" style="left:864px">
  <svg width="56" height="56" viewBox="0 0 56 56"><g fill="var(--blue-light)"><circle cx="28" cy="28" r="18"/><g id="teeth"><rect x="23" y="2" width="10" height="12"/><rect x="23" y="42" width="10" height="12"/><rect x="2" y="23" width="12" height="10"/><rect x="42" y="23" width="12" height="10"/></g><g transform="rotate(45 28 28)"><rect x="23" y="2" width="10" height="12"/><rect x="23" y="42" width="10" height="12"/><rect x="2" y="23" width="12" height="10"/><rect x="42" y="23" width="12" height="10"/></g></g><circle cx="28" cy="28" r="8" fill="#fff"/></svg>
  <h3>Lorem Ipsum</h3>
  <p>Sed ut perspiciatis unde omnis iste natus error sit voluptatem accusantium doloremque laudantium</p>
  <div class="btn">Read More</div>
</article>

<h2 class="abs display section-title" style="top:1198px">Gallery</h2>
<div class="abs photo" style="left:112px;top:1289px;width:270px;height:212px;background:linear-gradient(135deg,#2a2a2a,#8a5a30 55%,#3a3a3a)" role="img" aria-label="Bronze alloy wheel being fitted in a workshop"></div>
<div class="abs photo" style="left:112px;top:1512px;width:270px;height:366px;background:linear-gradient(135deg,#d8d8d8,#8a8a8a 50%,#222)" role="img" aria-label="Close-up of a silver multi-spoke alloy wheel"></div>
<div class="abs photo" style="left:416px;top:1290px;width:368px;height:367px;background:linear-gradient(135deg,#3a3e44,#8a5a3a 55%,#c8602a 75%,#2a2a2a)" role="img" aria-label="Technician in orange jacket repairing an alloy rim"></div>
<div class="abs photo" style="left:416px;top:1668px;width:368px;height:211px;background:linear-gradient(135deg,#111,#555 55%,#bbb)" role="img" aria-label="Tyre tread and silver alloy wheel close-up"></div>
<div class="abs photo" style="left:817px;top:1289px;width:270px;height:212px;background:linear-gradient(135deg,#1c2634,#7c8894 50%,#1a1a1a)" role="img" aria-label="Impact wrench tightening wheel nuts on an alloy wheel"></div>
<div class="abs photo" style="left:817px;top:1512px;width:270px;height:366px;background:linear-gradient(160deg,#2a3644,#9aa8b4 45%,#6a3a28 85%)" role="img" aria-label="Polished alloy wheel on a workbench"></div>

<h2 class="abs display section-title" style="top:1928px">Mission Statememt</h2>
<div class="abs mission-frame"></div>
<div class="abs mission-photo" role="img" aria-label="Gloved hand repairing the spokes of an alloy wheel"></div>
<p class="abs mission-text">Sed ut perspiciatis unde omnis iste natus error sit voluptatem accusantium doloremque laudantium, totam rem aperiam, eaque ipsa quae ab illo inventore veritatis et quasi architecto beatae vitae dicta sunt explicabo. Nemo enim ipsam voluptatem quia voluptas sit aspernatur aut odit aut fugit, sed quia consequuntur magni dolores eos qui ratione voluptatem sequi nesciunt. Neque porro quisquam est, qui dolorem ipsum quia dolor sit amet, consectetur, adipisci velit, sed quia non numquam eius modi tempora incidunt ut labore et dolore magnam aliquam quaerat voluptatem.</p>
<div class="btn" style="left:599px;top:2259px;width:114px;height:44px">Read More</div>

<footer class="abs footer"></footer>
<section class="abs clients-box"></section>
<h2 class="abs display section-title" style="top:2477px">Clients</h2>
<div class="abs arrow-btn" style="left:158px"><svg width="39" height="38" viewBox="0 0 39 38"><line x1="8" y1="19" x2="32" y2="19" stroke="#fff" stroke-width="2.5"/><polyline points="15,12 8,19 15,26" fill="none" stroke="#fff" stroke-width="2.5"/></svg></div>
<div class="abs arrow-btn" style="left:1002px"><svg width="39" height="38" viewBox="0 0 39 38"><line x1="7" y1="19" x2="31" y2="19" stroke="#fff" stroke-width="2.5"/><polyline points="24,12 31,19 24,26" fill="none" stroke="#fff" stroke-width="2.5"/></svg></div>
<div class="abs client-ring"><div class="abs client-photo" role="img" aria-label="Portrait of a smiling client"></div></div>
<div class="abs quote-mark" style="left:556px;top:2580px">&ldquo;</div>
<p class="abs client-quote">Sed ut perspiciatis unde omnis iste natus error sit voluptatem accusantium doloremque laudantium, totam rem aperiam, eaque ipsa quae ab illo inventore veritatis et quasi architecto beatae vitae dicta sunt explicabo. Nemo enim ipsam voluptatem quia voluptas sit aspernatur aut odit aut fugit.</p>
<div class="abs quote-mark" style="left:818px;top:2728px">&rdquo;</div>

<div class="abs footer-brand"><span class="brand-dot"></span>RIMCRAFT WORKS</div>
<nav class="footer-nav">
  <a style="left:332px">Home</a>
  <a style="left:446px">Services</a>
  <a style="left:578px">Gallery</a>
  <a style="left:700px">Clients</a>
  <a style="left:819px">Contact</a>
</nav>
<div class="abs footer-contact">
  <span><svg width="24" height="18" viewBox="0 0 24 18"><rect x="1" y="1" width="22" height="16" fill="none" stroke="#fff" stroke-width="1.6"/><polyline points="1,1 12,10 23,1" fill="none" stroke="#fff" stroke-width="1.6"/></svg>info@rimcraftworks.com</span>
  <span><svg width="22" height="22" viewBox="0 0 22 22"><path d="M5 2 L9 7 L7 9 Q9 13 13 15 L15 13 L20 17 L17 20 Q7 19 2 5 Z" fill="none" stroke="#fff" stroke-width="1.6"/></svg>0100 555 018</span>
</div>
<div class="abs copyright">© 2023 &nbsp;| Rimcraft Works &nbsp;All Rights Reserved</div>

</body>
</html>
```